Corporate Travel Technology Company needs new Business Card design

We need a new business card design to reflect our re-branded company. Our company is called tolven (pronounced tolvenn) and we provide Business Intelligence and mobile travel management solutions for the corporate travel industry. Our multinational customers use our solutions to manage large travel budgets and frequent travellers, as well as to save money and reduce risk. We'd like to see designs that use the blue and green palette as well as our corporate logo (attached below). The design should communicate innovation, insight, forward thinking, contemporary, trusted.

Target Market(s)

Large multinational corporates and Travel Agencies.

Industry/Entity Type

Business

Contact Information for Business Card

Rosalind Mercer
Chief Executive
tolven
Phone number - +61 (0)2 8134 2907
Email address - rosalind.mercer@tolven-example.com
Mobile number - +61 (0)438 516 702
www.tolven-example.com

Font styles to use
Other font styles liked:
• Please use font as close to corporate logo as possible

Colors
0255a3
0393ce
00a990
33b8a4
33a6d7
3176b5

Requirements
Must have
• Please include the words;
• Mobile Travel Management
• Accelerating Travel Business Insights
• Use corporate logo - although icon can be stylised if needed

```html
<!DOCTYPE html>
<html lang="en">
<head>
<meta charset="utf-8">
<title>tolven Business Card</title>
<link href="https://fonts.googleapis.com/css2?family=Source+Sans+3:wght@400;600;700&display=swap" rel="stylesheet">
<style>
  :root {
    --stage: #1c1c1c;
    --card-white: #ffffff;
    --brand-blue: #29abe2;
    --text-dark: #444a4a;
    --text-light: #ffffff;
  }
  * { margin: 0; padding: 0; box-sizing: border-box; }
  html, body {
    width: 1200px; height: 900px; overflow: hidden;
    background: var(--stage);
    font-family: "Source Sans 3", "Myriad Pro", sans-serif;
  }
  .stage { position: relative; width: 1200px; height: 900px; }

  .card {
    position: absolute; top: 170px;
    width: 347px; height: 561px;
  }
  .card--front { left: 259px; background: var(--card-white); }
  .card--back  { left: 631px; background: var(--brand-blue); }

  .accent-band {
    position: absolute; left: 102px;
    width: 143px; height: 30px;
    background: var(--brand-blue);
  }
  .accent-band--top { top: 0; }
  .accent-band--bottom { bottom: 0; height: 28px; }

  .wordmark {
    position: absolute; top: 168px; left: 0; width: 100%;
    display: flex; align-items: center; justify-content: center; gap: 12px;
    color: var(--text-dark);
    font-weight: 400; font-size: 72px; letter-spacing: 1px; line-height: 1;
  }
  .wordmark__dot {
    width: 18px; height: 18px; border-radius: 50%;
    background: var(--brand-blue);
  }

  .identity {
    position: absolute; top: 305px; left: 0; width: 100%;
    text-align: center;
  }
  .identity__name {
    color: var(--brand-blue);
    font-weight: 700; font-size: 19.5px; line-height: 22px;
  }
  .identity__role {
    color: var(--text-dark);
    font-size: 16px; line-height: 21px;
  }

  .contact-list {
    position: absolute; top: 374px; left: 0; width: 100%;
    list-style: none;
    display: flex; flex-direction: column; align-items: center;
  }
  .contact-list__item {
    display: flex; align-items: center; gap: 8px;
    color: var(--text-dark);
    font-size: 16.5px; line-height: 20.5px;
  }
  .contact-list__icon { width: 10px; height: 10px; fill: var(--brand-blue); flex: none; }

  .taglines {
    position: absolute; top: 456px; left: 0; width: 100%;
    text-align: center;
    color: var(--text-light);
    font-weight: 600; font-size: 17px; line-height: 21px;
  }
</style>
</head>
<body>
<main class="stage">

  <section class="card card--front" aria-label="Business card front">
    <div class="accent-band accent-band--top"></div>

    <div class="wordmark">
      <span class="wordmark__dot"></span>
      <span class="wordmark__name">tolven</span>
    </div>

    <div class="identity">
      <p class="identity__name">Rosalind Mercer</p>
      <p class="identity__role">Chief Executive</p>
    </div>

    <ul class="contact-list">
      <li class="contact-list__item">
        <svg class="contact-list__icon" viewBox="0 0 10 10" aria-hidden="true"><path d="M2 0.5 L3.6 2.6 L2.7 3.6 C3.3 5 4.8 6.6 6.3 7.3 L7.3 6.4 L9.5 8 L8.4 9.5 C4.5 9.2 0.8 5.5 0.5 1.6 Z"/></svg>
        <span>+61 (0)2 8134 2907</span>
      </li>
      <li class="contact-list__item">
        <svg class="contact-list__icon" viewBox="0 0 10 10" aria-hidden="true"><path d="M2.5 0 H7.5 V10 H2.5 Z M3.4 1.2 V7.8 H6.6 V1.2 Z M4.5 8.4 H5.5 V9.3 H4.5 Z" fill-rule="evenodd"/></svg>
        <span>+61 (0)438 516 702</span>
      </li>
      <li class="contact-list__item">
        <svg class="contact-list__icon" viewBox="0 0 10 10" aria-hidden="true"><path d="M0 2 H10 V8.5 H0 Z M0.8 2.6 L5 5.6 L9.2 2.6 Z" fill-rule="evenodd"/></svg>
        <span>rosalind.mercer@tolven-example.com</span>
      </li>
      <li class="contact-list__item">
        <svg class="contact-list__icon" viewBox="0 0 10 10" aria-hidden="true"><circle cx="5" cy="5" r="4.3" fill="none" stroke="var(--brand-blue)" stroke-width="1"/><ellipse cx="5" cy="5" rx="1.8" ry="4.3" fill="none" stroke="var(--brand-blue)" stroke-width="0.8"/><path d="M0.7 5 H9.3" stroke="var(--brand-blue)" stroke-width="0.8"/></svg>
        <span>www.tolven-example.com</span>
      </li>
    </ul>

    <div class="accent-band accent-band--bottom"></div>
  </section>

  <section class="card card--back" aria-label="Business card back">
    <div class="taglines">
      <p>Mobile Travel Management</p>
      <p>Accelerating Travel Business Insights</p>
    </div>
  </section>

</main>
</body>
</html>
```